Info Graphic Poster Needed

We need a poster illustrating how to put on Cryo gear. Instructions with some graphics next to them that are good examples of what to do..etc.
" How to put on gear for Cyro treatment
1. Remove clothing down to underwear or workout clothes
2. Socks and slippers
3. Facemask
4. Ear warmers
5. Gloves
6. Mittens
7. Wrap towel/robe over chest for women and over bottom for men if desired
8. Request robe if desired "
We would like our logo on the bottom of the poster (logo attached)
We like very modern designs.
Thank you!!

```html
<!DOCTYPE html>
<html lang="en">
<head>
<meta charset="utf-8">
<title>How to Put On Gear for Cryo Treatment</title>
<link href="https://fonts.googleapis.com/css2?family=Roboto:wght@300;400&family=Roboto+Condensed:wght@700&display=swap" rel="stylesheet">
<style>
  :root {
    --page-bg: #e3e6e7;
    --poster-light: #a6e5f1;
    --poster-glow: #f4fdff;
    --band-deep: #1f5f6b;
    --band-dark: #2f7482;
    --band-mid: #5aa6b3;
    --band-light: #93d3de;
    --hex-fill: #5197a3;
    --hex-edge: #1c4e59;
    --badge-fill: #3f8894;
    --art-light: #f3f6f7;
    --art-shade: #b4c3c7;
    --text-dark: #1c3e46;
    --title-color: #17444f;
    --brand-color: #23409a;
  }
  html, body {
    margin: 0;
    width: 1004px;
    height: 1200px;
    overflow: hidden;
    background: var(--page-bg);
  }
  .poster {
    position: absolute;
    left: 78px;
    top: 0;
    width: 847px;
    height: 1200px;
    display: block;
  }
  .step-label {
    font-family: "Roboto", Arial, sans-serif;
    font-weight: 400;
    font-size: 19px;
    fill: var(--text-dark);
    text-anchor: middle;
  }
  .title {
    font-family: "Roboto Condensed", "Arial Narrow", sans-serif;
    font-weight: 700;
    font-size: 39px;
    fill: var(--title-color);
    text-anchor: middle;
  }
  .hex {
    fill: var(--hex-fill);
    stroke: var(--hex-edge);
    stroke-width: 2;
  }
  .step-art {
    fill: url(#artTone);
  }
  .badge circle {
    fill: var(--badge-fill);
    stroke: var(--hex-edge);
    stroke-width: 2.5;
  }
  .badge text {
    font-family: "Roboto Condensed", "Arial Narrow", sans-serif;
    font-weight: 700;
    font-size: 32px;
    fill: #ffffff;
    text-anchor: middle;
  }
  .brand-name {
    font-family: "Roboto", Arial, sans-serif;
    font-weight: 300;
    font-size: 58px;
    fill: var(--brand-color);
  }
</style>
</head>
<body>
<svg class="poster" viewBox="0 0 971 1375" xmlns="http://www.w3.org/2000/svg" aria-labelledby="poster-title">
  <defs>
    <radialGradient id="centerGlow" cx="0.5" cy="0.55" r="0.5">
      <stop offset="0" stop-color="var(--poster-glow)"/>
      <stop offset="0.45" stop-color="var(--poster-light)"/>
      <stop offset="1" stop-color="var(--poster-light)"/>
    </radialGradient>
    <linearGradient id="bandTop" x1="0" y1="0.2" x2="1" y2="0.8">
      <stop offset="0" stop-color="var(--band-mid)"/>
      <stop offset="0.3" stop-color="var(--band-deep)"/>
      <stop offset="0.55" stop-color="var(--band-light)"/>
      <stop offset="0.8" stop-color="var(--band-dark)"/>
      <stop offset="1" stop-color="var(--band-light)"/>
    </linearGradient>
    <linearGradient id="bandBottom" x1="0" y1="1" x2="1" y2="0">
      <stop offset="0" stop-color="var(--band-light)"/>
      <stop offset="0.5" stop-color="var(--band-mid)"/>
      <stop offset="0.8" stop-color="var(--band-deep)"/>
      <stop offset="1" stop-color="var(--band-mid)"/>
    </linearGradient>
    <linearGradient id="artTone" x1="0" y1="0" x2="1" y2="1">
      <stop offset="0" stop-color="var(--art-light)"/>
      <stop offset="1" stop-color="var(--art-shade)"/>
    </linearGradient>
    <polygon id="hexShape" points="-114,0 -57,-99 57,-99 114,0 57,99 -57,99"/>
  </defs>

  <rect width="971" height="1375" fill="url(#centerGlow)"/>
  <path role="img" aria-label="Faceted teal geometric band" d="M0,0 H971 V20 C900,160 760,205 600,218 C400,232 150,245 0,345 Z" fill="url(#bandTop)"/>
  <path role="img" aria-label="Faceted teal geometric band" d="M370,1375 C620,1330 900,1250 971,1110 V1375 Z" fill="url(#bandBottom)"/>

  <text id="poster-title" class="title">
    <tspan x="485" y="676">HOW</tspan>
    <tspan x="485" y="724">TO PUT ON GEAR</tspan>
    <tspan x="485" y="772">FOR CRYO</tspan>
    <tspan x="485" y="820">TREATMENT</tspan>
  </text>

  <g class="step step-1">
    <use href="#hexShape" class="hex" transform="translate(478,450)"/>
    <rect class="step-art" role="img" aria-label="Man and woman in underwear or workout clothes" x="432" y="362" width="92" height="176" rx="10"/>
    <g class="badge"><circle cx="483" cy="558" r="27"/><text x="483" y="569">1</text></g>
    <text class="step-label"><tspan x="476" y="283">Remove clothing down</tspan><tspan x="476" y="306">to underwear</tspan><tspan x="476" y="329">or workout clothes</tspan></text>
  </g>

  <g class="step step-2">
    <use href="#hexShape" class="hex" transform="translate(680,548)"/>
    <rect class="step-art" role="img" aria-label="Man and woman wearing socks and slippers" x="630" y="462" width="104" height="176" rx="10"/>
    <g class="badge"><circle cx="593" cy="589" r="27"/><text x="593" y="600">2</text></g>
    <text class="step-label" x="682" y="430">Socks and slippers</text>
  </g>

  <g class="step step-3">
    <use href="#hexShape" class="hex" transform="translate(763,760)"/>
    <rect class="step-art" role="img" aria-label="Woman and man wearing black facemasks" x="676" y="714" width="184" height="62" rx="10"/>
    <g class="badge"><circle cx="645" cy="761" r="27"/><text x="645" y="772">3</text></g>
    <text class="step-label" x="813" y="642">Facemask</text>
  </g>

  <g class="step step-4">
    <use href="#hexShape" class="hex" transform="translate(667,971)"/>
    <rect class="step-art" role="img" aria-label="Side profile of a woman wearing ear warmers" x="628" y="874" width="92" height="188" rx="10"/>
    <g class="badge"><circle cx="584" cy="921" r="27"/><text x="584" y="932">4</text></g>
    <text class="step-label" x="670" y="1104">Ear warmers</text>
  </g>

  <g class="step step-5">
    <use href="#hexShape" class="hex" transform="translate(478,1068)"/>
    <rect class="step-art" role="img" aria-label="Pair of white gloves" x="420" y="994" width="100" height="166" rx="10"/>
    <g class="badge"><circle cx="484" cy="959" r="27"/><text x="484" y="970">5</text></g>
    <text class="step-label" x="478" y="1202">Gloves</text>
  </g>

  <g class="step step-6">
    <use href="#hexShape" class="hex" transform="translate(285,971)"/>
    <rect class="step-art" role="img" aria-label="Pair of knitted grey mittens" x="192" y="920" width="166" height="116" rx="10"/>
    <g class="badge"><circle cx="366" cy="921" r="27"/><text x="366" y="932">6</text></g>
    <text class="step-label" x="282" y="1106">Mittens</text>
  </g>

  <g class="step step-7">
    <use href="#hexShape" class="hex" transform="translate(210,760)"/>
    <rect class="step-art" role="img" aria-label="Man with towel around waist and woman with towel over chest" x="162" y="676" width="106" height="174" rx="10"/>
    <g class="badge"><circle cx="334" cy="761" r="27"/><text x="334" y="772">7</text></g>
    <text class="step-label">
      <tspan x="60" y="675">Wrap</tspan>
      <tspan x="60" y="698">towel/robe</tspan>
      <tspan x="60" y="722">over chest</tspan>
      <tspan x="60" y="745">for women</tspan>
      <tspan x="60" y="768">and over</tspan>
      <tspan x="60" y="792">bottom for</tspan>
      <tspan x="60" y="815">men</tspan>
      <tspan x="60" y="839">if desired</tspan>
    </text>
  </g>

  <g class="step step-8">
    <use href="#hexShape" class="hex" transform="translate(282,548)"/>
    <rect class="step-art" role="img" aria-label="White bathrobe" x="242" y="458" width="84" height="178" rx="10"/>
    <g class="badge"><circle cx="368" cy="589" r="27"/><text x="368" y="600">8</text></g>
    <text class="step-label"><tspan x="276" y="407">Request robe</tspan><tspan x="276" y="430">if desired</tspan></text>
  </g>

  <text class="brand-name" x="17" y="1318">Arcline Health</text>
</svg>
</body>
</html>
```